Marvani Trinkets
Lorraine Whitcomb Designs
Marvani Trinkets -
Creative Brief
Simple
Lorraine Whitcomb
Jewelry Designer
2718 Quillan Ave Dallas TX 75219
lorraine@marvani-example.com
www.marvani-example.com
Please do a few designs!
Maybe just the logo?

```html
<!DOCTYPE html>
<html lang="en">
<head>
<meta charset="utf-8">
<title>Marvani Trinkets – Business Card</title>
<link rel="stylesheet" href="https://fonts.googleapis.com/css2?family=Open+Sans:ital,wght@0,400;0,600;1,600&display=swap">
<style>
  :root {
    --bg: #ece9e4;
    --card: #ffffff;
    --ink: #4a4a4a;
    --ink-soft: #5e5e5e;
    --teal: #14b3b0;
    --teal-deep: #0a8f8c;
    --teal-light: #3fe0dc;
    --silver: #b9b9b9;
    --silver-light: #e6e6e6;
  }
  * { box-sizing: border-box; margin: 0; padding: 0; }
  html, body {
    width: 1200px; height: 935px; overflow: hidden;
    background: var(--bg);
    font-family: "Open Sans", Arial, sans-serif;
  }
  .business-card {
    position: absolute; left: 100px; top: 182px;
    width: 1000px; height: 571px;
    background: var(--card);
    border-radius: 48px;
    overflow: hidden;
    box-shadow: 0 10px 28px rgba(0,0,0,0.18);
  }
  .swoosh { position: absolute; left: 0; top: 0; width: 1000px; height: 571px; }
  .contact-block {
    position: absolute; right: 70px; top: 92px;
    text-align: right; color: var(--ink-soft);
  }
  .contact-name { font-size: 38px; font-weight: 600; color: var(--ink); line-height: 1.2; }
  .contact-title { font-size: 26px; font-weight: 600; font-style: italic; color: var(--ink); margin-bottom: 38px; }
  .contact-line { font-size: 24px; line-height: 1.36; }
  .contact-line b { font-weight: 600; color: var(--ink); }
  .brand {
    position: absolute; left: 56px; top: 300px;
    display: flex; align-items: center; gap: 16px;
  }
  .brand-dot { width: 30px; height: 30px; border-radius: 50%; background: var(--teal); }
  .brand-name { font-size: 50px; font-weight: 400; color: var(--ink); letter-spacing: 0.5px; }
</style>
</head>
<body>
  <div class="business-card">
    <svg class="swoosh" viewBox="0 0 1000 571" aria-hidden="true">
      <defs>
        <linearGradient id="tealBand" x1="0" y1="0" x2="1" y2="0">
          <stop offset="0" stop-color="var(--teal-deep)"/>
          <stop offset="0.55" stop-color="var(--teal-light)"/>
          <stop offset="1" stop-color="var(--teal)"/>
        </linearGradient>
        <linearGradient id="silverBand" x1="0" y1="0" x2="1" y2="0">
          <stop offset="0" stop-color="var(--silver-light)"/>
          <stop offset="0.5" stop-color="var(--silver)"/>
          <stop offset="1" stop-color="var(--silver-light)"/>
        </linearGradient>
      </defs>
      <path fill="url(#silverBand)" d="M0,500 C220,430 480,520 720,445 C830,410 920,385 1000,372 L1000,398 C920,410 830,438 720,472 C480,548 230,470 0,528 Z"/>
      <path fill="url(#tealBand)" d="M0,528 C230,470 480,548 720,472 C830,438 920,410 1000,398 L1000,571 L0,571 Z"/>
    </svg>

    <div class="brand">
      <span class="brand-dot"></span>
      <span class="brand-name">Marvani Trinkets</span>
    </div>

    <div class="contact-block">
      <p class="contact-name">Lorraine Whitcomb</p>
      <p class="contact-title">Jewelry Designer</p>
      <p class="contact-line">2718 Quillan Ave Dallas TX 75219</p>
      <p class="contact-line"><b>Phone :</b> 214-555-0187</p>
      <p class="contact-line"><b>Email :</b> lorraine@marvani-example.com</p>
      <p class="contact-line"><b>Web :</b> www.marvani-example.com</p>
    </div>
  </div>
</body>
</html>
```